Brookvane Consulting Business Card Design

Business Card Design for Brookvane Consulting. Brookvane Consulting is a boutique consultancy based in Atlanta, GA., that specializes in marketing strategy, organization planning, and leadership development. We provide solutions for small businesses and startups as well as Vantage 300 companies.

http://brookvaneconsulting.com/

Target Market(s)

We provide solutions for small businesses and startups as well as Vantage 300 companies.

Industry/Entity Type

Consulting

Contact Information for Business Card

Two sided business card with priority on contact information, logo, tag line (Insight to Plan Bolder, Act Sooner, Grow Further)

Colors

Designer to choose colors to be used in the design.

Requirements
Must have
• contact information, logo, tag line (Insight to Plan Bolder, Act Sooner, Grow Further)
• Simple no over communication.
Nice to have
• I would like to see different placements of logo and creative use of both sides of the card
Should not have
• Do not put too much information on the card.

```html
<!DOCTYPE html>
<html lang="en">
<head>
<meta charset="UTF-8">
<title>Brookvane Consulting – Business Card</title>
<link href="https://fonts.googleapis.com/css2?family=Montserrat:wght@600&family=Roboto:wght@400&family=Kaushan+Script&display=swap" rel="stylesheet">
<style>
  :root {
    --backdrop: #1e1e1e;
    --card: #3a3a3a;
    --band: #0d0d0d;
    --ink: #ffffff;
    --ink-soft: #e6e6e6;
  }
  * { margin: 0; padding: 0; box-sizing: border-box; }
  html, body {
    width: 799px; height: 1200px; overflow: hidden;
    background: var(--backdrop);
  }
  .sheet { position: relative; width: 799px; height: 1200px; }
  .card {
    position: absolute; left: 80px;
    width: 640px; height: 366px;
    background: var(--card);
    border-radius: 26px;
    overflow: hidden;
    box-shadow: 0 10px 30px rgba(0,0,0,0.5);
  }
  .card--front { top: 150px; }
  .card--back { top: 680px; }

  .wordmark {
    font-family: "Montserrat", sans-serif;
    font-weight: 600;
    color: var(--ink);
    display: flex; align-items: center; gap: 14px;
    white-space: nowrap;
  }
  .wordmark__dot {
    width: 18px; height: 18px; background: var(--ink); display: inline-block; flex: none;
  }
  .card--front .wordmark {
    position: absolute; left: 0; right: 0; top: 150px;
    justify-content: center;
    font-size: 44px; letter-spacing: 1px;
  }

  .tagline-band {
    position: absolute; left: 0; top: 0; bottom: 0; width: 44px;
    background: var(--band);
  }
  .tagline {
    position: absolute; left: 22px; top: 183px;
    transform: translate(-50%, -50%) rotate(-90deg);
    white-space: nowrap;
    font-family: "Roboto", sans-serif; font-size: 14px;
    color: var(--ink);
  }
  .card--back .wordmark {
    position: absolute; left: 130px; top: 56px;
    font-size: 36px;
  }
  .contact {
    position: absolute; left: 100px; top: 200px;
    font-family: "Roboto", sans-serif; color: var(--ink-soft);
    font-size: 16px; line-height: 22px;
  }
  .contact__name {
    font-family: "Kaushan Script", cursive;
    font-size: 26px; color: var(--ink); margin-bottom: 8px; line-height: 30px;
  }
</style>
</head>
<body>
<main class="sheet">
  <section class="card card--front" aria-label="Card front">
    <div class="wordmark"><span class="wordmark__dot"></span>Brookvane Consulting</div>
  </section>

  <section class="card card--back" aria-label="Card back">
    <div class="tagline-band"></div>
    <p class="tagline">Insight to Plan Bolder, Act Sooner, Grow Further</p>
    <div class="wordmark"><span class="wordmark__dot"></span>Brookvane Consulting</div>
    <div class="contact">
      <p class="contact__name">Dalen</p>
      <p>555-014-2290</p>
      <p>dalen@brookvaneconsulting.com</p>
      <p>www.brookvaneconsulting.com</p>
    </div>
  </section>
</main>
</body>
</html>
```